Lip Balm Label Design

Design a label for a Lavender-Mint lip balm. We make high-quality natural essential oil products. Please use the old label as an example of what exists. The label should include purple. The final design should be eye-catching and distinct. The file should be in an AI file.

Here is the information that should be included on the label:
1) ingredients:Theobroma Cacao (Cocoa) Seed Butter, Theobroma grandiflorum Ultra Refined Butter, beesewax, Calendula Officinalis Flower Oil, Prunus Amygdalus Dulcis (Sweet Almond) Oil, cetyl alcohol and Tocopherol. Lavandula Angustifolia (Lavender) Oil and Mentha Piperita (Peppermint) Oil.

2) www.kelsoroothaven.com

3) Brand name and logo: K. Elso Aromatherapy (logo is attached- you can use with form)

```html
<!DOCTYPE html>
<html lang="en">
<head>
<meta charset="utf-8">
<title>K. Elso Aromatherapy – Lavender Mint Lip Balm Label</title>
<link rel="stylesheet" href="https://fonts.googleapis.com/css2?family=Oswald:wght@300&family=Playfair+Display:wght@400&family=Lora&display=swap">
<style>
  :root {
    --page: #ffffff;
    --violet-edge: #6a5fd6;
    --violet-mid: #453b8c;
    --violet-core: #1f1d40;
    --panel: #e2defc;
    --ink: #1a1a1a;
    --accent: #7a6de0;
    --url: #e4e0ff;
  }
  html, body {
    margin: 0;
    width: 1200px;
    height: 1000px;
    overflow: hidden;
    background: var(--page);
  }
  .canvas {
    position: relative;
    width: 1200px;
    height: 1000px;
  }
  .label {
    position: absolute;
    left: 222px;
    top: 217px;
    width: 756px;
    height: 566px;
    background: linear-gradient(90deg, var(--violet-edge) 0%, var(--violet-mid) 20%, var(--violet-core) 50%, var(--violet-mid) 80%, var(--violet-edge) 100%);
    overflow: hidden;
  }
  .ingredients {
    position: absolute;
    left: 11px;
    top: 42px;
    width: 127px;
    height: 484px;
    box-sizing: border-box;
    padding: 12px 12px 12px 10px;
    background: var(--panel);
    border-radius: 16px;
    writing-mode: vertical-rl;
    font-family: "Oswald", sans-serif;
    font-weight: 300;
    font-size: 17px;
    line-height: 27px;
    color: var(--ink);
  }
  .ingredients-line {
    display: block;
    white-space: nowrap;
  }
  .ingredients-line--full {
    text-align: justify;
    text-align-last: justify;
    white-space: normal;
  }
  .ingredients-heading {
    color: var(--accent);
  }
  .brand-name {
    position: absolute;
    left: 178px;
    top: 96px;
    width: 400px;
    margin: 0;
    text-align: center;
    font-family: "Lora", serif;
    font-weight: 400;
    font-size: 30px;
    line-height: 40px;
    color: var(--url);
  }
  .sprig-wreath {
    position: absolute;
    left: 200px;
    top: 316px;
    width: 356px;
    height: 234px;
    border-radius: 0 0 180px 180px;
    background: radial-gradient(ellipse at 50% 90%, rgba(109,143,54,0.75) 0%, rgba(143,111,216,0.55) 45%, rgba(143,111,216,0) 75%);
  }
  .flavour {
    position: absolute;
    left: 299px;
    top: 287px;
    width: 158px;
    height: 103px;
    background: #ffffff;
    border-radius: 14px;
    display: flex;
    flex-direction: column;
    align-items: center;
    justify-content: center;
    font-family: "Playfair Display", serif;
    font-size: 40px;
    line-height: 44px;
    color: var(--accent);
  }
  .flavour span {
    display: block;
    transform: scaleX(0.62);
    white-space: nowrap;
  }
  .website {
    position: absolute;
    left: 716px;
    top: 112px;
    writing-mode: vertical-rl;
    font-family: "Lora", serif;
    font-size: 21px;
    color: var(--url);
    white-space: nowrap;
  }
</style>
</head>
<body>
<div class="canvas">
  <section class="label">
    <div class="ingredients">
      <span class="ingredients-line ingredients-line--full"><span class="ingredients-heading">INGREDIENTS:</span> Theobroma Cacao (Cocoa) Seed Butter, Theobroma</span>
      <span class="ingredients-line">grandiflorum Ultra Refined Butter, beesewax, Calendula Officinalis Flower Oil,</span>
      <span class="ingredients-line">Prunus Amygdalus Dulcis (Sweet Almond) Oil, cetyl alcohol and Tocopherol.</span>
      <span class="ingredients-line">Lavandula Angustifolia (Lavender) Oil and Mentha Piperita (Peppermint) Oil.</span>
    </div>

    <p class="brand-name">K. Elso Aromatherapy</p>

    <div class="sprig-wreath" role="img" aria-label="Illustrated wreath of lavender sprigs and green leaves framing the product name"></div>

    <div class="flavour">
      <span>LAVENDER</span>
      <span>MINT</span>
    </div>

    <div class="website">www.kelsoroothaven.com</div>
  </section>
</div>
</body>
</html>
```